Media Services Start-up -- Corporate Website and Logo Design. Inspiration required!

We need a logo design and corporate website design, including coding, for our start-up business.
Vennatra’s value proposition is based on bringing together media content from a vast number of geographies globally, adding human and AI curation, translation and editing, and delivering the content using tailored customer interfaces. On the one hand, the business brings together media coverage from all over the world, and on the other it brings together content, human skills and technology to deliver a supreme customer experience.
Vennatra is a B2B media monitoring and analytics business with emphasis on global customers. Vennatra's service offering is centred around sourcing media content from different markets, processing, storing and delivering the content and insights derived from it using an online platform / mobile app.
The messaging we want to create through the logo is:
- Global scope
- Speed of delivery
- Cost-efficiency
- Multi-lingual
- Tailor-made
- Trustworthy
Target Market(s)
Business to business, PR / Communications, Media, Marketing
Logo Text
Vennatra
Coding
Coded - Design and coding required
Number of Pages Required
5+ page
Font styles to use
Other font styles liked:
- See Design Brief for details
Colors
Designer to choose colors to be used in the design.

```html
<!DOCTYPE html>
<html lang="en">
<head>
<meta charset="utf-8">
<title>Vennatra — Our People</title>
<link rel="stylesheet" href="https://fonts.googleapis.com/css2?family=Roboto:wght@400;500;700&display=swap">
<style>
  :root{
    --header-bg:#1b1b1b;
    --page-bg:#141414;
    --teal:#37ae9a;
    --teal-text:#3fbfa9;
    --white:#ffffff;
    --logo:#e2e2e2;
    --muted:#f0f0f0;
    --avatar-fill:#eef1f3;
  }
  *{box-sizing:border-box;margin:0;padding:0}
  html,body{width:1200px;height:713px;overflow:hidden;background:var(--page-bg);font-family:'Roboto',sans-serif;color:var(--white)}
  .page{position:relative;width:1200px;height:713px}
  .hero-backdrop{position:absolute;left:0;top:85px;width:1200px;height:593px;
    background:radial-gradient(circle at 600px 250px,#3a3a3a 0,#262626 140px,#1a1a1a 320px,#0e0e0e 600px),#111;}
  .site-header{position:absolute;left:0;top:0;width:1200px;height:85px;background:var(--header-bg)}
  .logo{position:absolute;left:141px;top:12px;font-size:49px;font-weight:700;color:var(--logo);letter-spacing:-0.5px}
  .contact{position:absolute;top:11px;display:flex;align-items:center;gap:9px;font-size:14px}
  .contact.phone{left:733px}
  .contact.mail{left:900px}
  .contact svg{width:27px;height:27px}
  .main-nav{position:absolute;top:53px;left:0;font-size:14px}
  .main-nav a{position:absolute;white-space:nowrap;color:var(--white);text-decoration:none}
  .main-nav a.active{color:var(--teal-text);font-weight:500}
  .sign-in{position:absolute;left:974px;top:49px;width:85px;height:29px;background:var(--teal);color:var(--white);font-size:15.5px;display:flex;align-items:center;justify-content:center}
  .intro{position:absolute;left:0;top:136px;width:1200px;text-align:center}
  .intro h1{font-size:32px;font-weight:700}
  .intro p{margin:13px auto 0;width:860px;font-size:14px;font-weight:500;line-height:22.5px}
  .member{position:absolute;top:286px;width:270px;text-align:center}
  .avatar{width:110px;height:110px;margin:0 auto;border:3px solid var(--teal);background:var(--avatar-fill)}
  .member h2{margin-top:22px;font-size:17px;font-weight:500;text-transform:uppercase}
  .member .role{margin-top:5px;font-size:13px}
  .member .bio{margin-top:18px;font-size:12.8px;line-height:20.4px;color:var(--muted)}
  .site-footer{position:absolute;left:0;top:678px;width:1200px;height:35px;background:var(--teal);font-size:13px}
  .site-footer .copy{position:absolute;left:141px;top:9px}
  .social{position:absolute;left:998px;top:10px;display:flex;gap:9px}
  .social span{width:15px;height:15px;border-radius:50%;background:var(--white)}
</style>
</head>
<body>
<div class="page">
  <div class="hero-backdrop" role="img" aria-label="Dark night city skyline with a businessman facing a glowing globe, connected by network lines to technology icons"></div>

  <header class="site-header">
    <div class="logo">Vennatra</div>
    <div class="contact phone">
      <svg viewBox="0 0 28 28"><circle cx="14" cy="14" r="12.5" fill="none" stroke="#fff" stroke-width="1.3"/><path d="M10 8.5l2.2-.6 1.3 3-1.4 1.1c.6 1.5 1.7 2.6 3.1 3.2l1.1-1.4 3 1.3-.6 2.2c-4.6.3-9-4.2-8.7-8.8z" fill="#fff"/></svg>
      <span>+1 555 204 8817</span>
    </div>
    <div class="contact mail">
      <svg viewBox="0 0 28 28"><circle cx="14" cy="14" r="12.5" fill="none" stroke="#fff" stroke-width="1.3"/><rect x="8" y="10" width="12" height="8.5" fill="none" stroke="#fff" stroke-width="1.3"/><path d="M8 10l6 5 6-5" fill="none" stroke="#fff" stroke-width="1.3"/></svg>
      <span>info@vennatra.com</span>
    </div>
    <nav class="main-nav">
      <a style="left:498px">Home</a>
      <a style="left:562px">Solutions</a>
      <a style="left:648px">How We Do It</a>
      <a class="active" style="left:760px">Our People</a>
      <a style="left:856px">Our Technology</a>
    </nav>
    <a class="sign-in">SIGN IN</a>
  </header>

  <section class="intro">
    <h1>Our People</h1>
    <p>We are a team of experienced and competent media intelligence professionals with 10+ years experience in delivering global solutions to the PR &amp; Communications community.</p>
  </section>

  <article class="member" style="left:152px">
    <div class="avatar" role="img" aria-label="Portrait of the CEO and founder"></div>
    <h2>Mira Castellan</h2>
    <p class="role">CEO &amp; Founder</p>
    <p class="bio">Mira is the founder and CEO of Vennatra, bringing nearly 20 years of experience in the business information and media intelligence domain. Mira leads Vennatra's business growth and strategic customer relationships.</p>
  </article>

  <article class="member" style="left:465px">
    <div class="avatar" role="img" aria-label="Portrait of a team member"></div>
    <h2>Elsa Norwyn</h2>
    <p class="role">Team</p>
    <p class="bio">Vennatra is the people who work in it. Vennatra is a team of content and media intelligence professionals, bringing media, communications, monitoring and measurement experience to its customers.</p>
  </article>

  <article class="member" style="left:779px">
    <div class="avatar" role="img" aria-label="Portrait of an expertise lead"></div>
    <h2>Leo Barrent</h2>
    <p class="role">Expertise</p>
    <p class="bio">The Vennatra team have in-market experience with media content in all EMEA markets, North America, South America and Asia. The team consists of knowledge centres within the Finance, Automotive, FMCG, Government, Non Profit, Retail, Hospitality, Pharmaceuticals sectors around the world.</p>
  </article>

  <footer class="site-footer">
    <p class="copy">Copyright © 2019 Vennatra. All Rights Reserved.</p>
    <div class="social"><span></span><span></span><span></span></div>
  </footer>
</div>
</body>
</html>
```